tinyTally Resource Book - 10 maths tasks to do outside

I need a 22 (11 pages back to back) page A6 sized book produced to standard for submission to professional printer. Needs to be as .pdf file showing guide lines and allowances for colour bleed. I have text already written and submitted as attachment in a Word file with margins set to A6 size. The theme of the materials is "Nature Play" so using lots of pictures from nature (Australia preferably) and showing lots of patterns in nature (rocks, leaves, flower petals etc). Some of the tasks refer to specific activities, such as "shadows" and "floating" so would be great to illustrate appropriately. The big emphasis is on learning outside the classroom, getting kids to engage actively with nature. I would like to see the pages as full colour - so not white background. The book itself will be spiral bound along the top edge so a margin of at least 1cm will be required at the top of each page (or the bottom of even numbered pages). Book will be printed on plastic laminated matte paper for outdoor use. Font size needs to be big enough to read. Fonts sizes, alignments and page numbers are all different at the moment and need to be standardised. One photo is included in a page as a sample if you can use it, otherwise disregard. Logo for Wattlebrook Numeracy Guild is also included to have as part of the acknowledgements at the back of the book.

Target Market(s)

Book is for early childhood and preschool teachers.

Industry/Entity Type

Education

Font styles to use
Sans Serif

Requirements
Must have
• Colour and appeal.
Nice to have
• Use of natural colours instead of bright catchy colours but that is your call.
Should not have
• American spelling

```html
<!DOCTYPE html>
<html lang="en-AU">
<head>
<meta charset="utf-8">
<title>Informal Units for Measuring Distance</title>
<link rel="stylesheet" href="https://fonts.googleapis.com/css2?family=Fredoka:wght@600&family=Didact+Gothic&display=swap">
<style>
  :root {
    --paper: #ffffff;
    --trim: #6b6b6b;
    --heading: #2d3a8e;
    --body: #2a2622;
    --bullet: #d8262e;
    --sea-top: #7fcbe6;
    --sea-mid: #bfe3ee;
    --sand-light: #efebe4;
    --sand-deep: #e2dacd;
  }
  * { box-sizing: border-box; margin: 0; padding: 0; }
  html, body { width: 892px; height: 1200px; overflow: hidden; background: var(--paper); }
  .page { position: relative; width: 892px; height: 1200px; }
  .crop-marks { position: absolute; inset: 0; }
  .bleed-photo {
    position: absolute; left: 53px; top: 53px; width: 787px; height: 1093px;
    background: linear-gradient(178deg, var(--sea-top) 0%, var(--sea-mid) 16%, #dfeef0 26%, var(--sand-light) 38%, var(--sand-light) 70%, var(--sand-deep) 100%);
  }
  .card-title, .section-heading {
    position: absolute; left: 126px; white-space: nowrap;
    font-family: "Fredoka", "Arial Rounded MT Bold", sans-serif; font-weight: 600;
    color: var(--heading);
    text-shadow: 0 0 2px #fff, 0 0 3px #fff, 1px 1px 0 #fff, -1px -1px 0 #fff, 1px -1px 0 #fff, -1px 1px 0 #fff;
  }
  .card-title { top: 139px; font-size: 54px; line-height: 54px; letter-spacing: 1.5px; }
  .section-heading { font-size: 48px; line-height: 48px; letter-spacing: 0.5px; }
  .task-list {
    position: absolute; left: 184px; list-style: none; white-space: nowrap;
    font-family: "Didact Gothic", "Century Gothic", sans-serif;
    font-size: 34px; line-height: 42.4px; color: var(--body);
  }
  .task-list li { position: relative; padding-left: 34px; }
  .task-list li::before {
    content: ""; position: absolute; left: 6px; top: 13px;
    width: 16px; height: 16px; background: var(--bullet); transform: rotate(45deg);
  }
</style>
</head>
<body>
<div class="page">
  <div class="bleed-photo" role="img" aria-label="Photograph of a white sandy beach with the sea along the top, weathered wooden posts standing in the sand and five twigs of different lengths laid out on the lower right"></div>

  <svg class="crop-marks" width="892" height="1200" viewBox="0 0 892 1200" aria-hidden="true">
    <g stroke="var(--trim)" stroke-width="0.8" fill="none">
      <path d="M53 0V40M0 53H40M75 35V75H35"/>
      <path d="M839 0V40M892 53H852M817 35V75H857"/>
      <path d="M53 1200V1160M0 1146H40M75 1165V1125H35"/>
      <path d="M839 1200V1160M892 1146H852M817 1165V1125H857"/>
    </g>
  </svg>

  <h1 class="card-title">11. Informal Units for<br>Measuring Distance</h1>

  <ul class="task-list" style="top:256px">
    <li>Get a long stick</li>
    <li>Use the stick to measure the distance<br>between 2 places</li>
    <li>Count each time you place down the<br>stick and then move it on</li>
    <li>Try with a different stick</li>
  </ul>

  <h2 class="section-heading" style="top:522px">Prompting questions</h2>
  <ul class="task-list" style="top:575px">
    <li>How far is 5 “sticks”? 10 “sticks”? etc</li>
    <li>Is the measurement the same when<br>you change the stick?</li>
  </ul>

  <h2 class="section-heading" style="top:710px">Variations</h2>
  <ul class="task-list" style="top:768px">
    <li>Try with different length<br>sticks or different objects</li>
  </ul>

  <h2 class="section-heading" style="top:862px">Big Ideas</h2>
  <ul class="task-list" style="top:918px">
    <li>Length</li>
    <li>Repeat</li>
    <li>Measure</li>
    <li>Compare</li>
  </ul>
</div>
</body>
</html>
```